Business card design for a teacher - double sided, sleek design.

My name is Lina and I am an online Arabic language teacher. I am looking for a beautiful business card design for my online teaching business.

The cards will be printed in 85mm x 55mm size.
The card can be either portrait or landscape.

The design should contain my logo on one side and information on the other.

The design needs to be clean and modern. Use of subtle Arabic geometric patterns would be nice. Icons for the social media information on the card should also match the design theme.

My logo font is Consolas, which is a Monospace font.

Business card design should be delivered with editable PSD or EPS files in the handover.

Thanks

Lina

----

Information on the back:

URL: www.speakwithnadia.net [this should stand out more than other details]
Email: info@speakwithnadia.net
Instagram: @speakwithnadia
Facebook: /speakwithnadia
Skype: speakwithnadia

My brand colours are shown in the logo attached. These are:
- Teal green - 4DC9C1
- Mango yellow - FFD600

Target Market(s)

- Young professionals
- Expatriates
- Women and Men

Industry/Entity Type

Education

Contact Information for Business Card

Information on the back:

Skype: speakwithnadia

- Teal green - 4DC9C1
- Mango yellow - FFD600

Font styles to use
Other font styles liked:
• Any font complimentary to my logo font which is a Monospace font called Consolas.

Colors

Designer to choose colors to be used in the design.

Requirements
Must have
• - Aesthetically pleasing look
• - Complimentary design with existing logo
Nice to have
• Arabic geometrical patterns

```html
<!DOCTYPE html>
<html lang="en">
<head>
<meta charset="utf-8">
<title>Nadia Tutoring – Business Card</title>
<link rel="stylesheet" href="https://fonts.googleapis.com/css2?family=Inconsolata:wght@400;600&family=Open+Sans:wght@400;600&display=swap">
<style>
  :root {
    --teal: #4dc9c1;
    --ink: #5f6163;
    --ink-soft: #8a8c8e;
    --paper: #ffffff;
    --pattern-base: #f3f4ee;
    --pattern-tint: #dff2ef;
    --backdrop: #e6e2db;
  }
  * { box-sizing: border-box; margin: 0; padding: 0; }
  html, body {
    width: 1200px; height: 886px; overflow: hidden;
    background: var(--backdrop);
  }
  .canvas {
    position: relative; width: 1200px; height: 886px;
    display: flex; align-items: center; justify-content: center; gap: 50px;
  }
  .card {
    position: relative; width: 520px; height: 336px;
    background: var(--paper);
    box-shadow: 0 6px 18px rgba(0,0,0,0.12);
    overflow: hidden;
  }

  /* Information side */
  .card--info { border-bottom: 10px solid var(--teal); }
  .contact-list {
    position: absolute; inset: 0 0 10px 0;
    display: flex; flex-direction: column; align-items: center; justify-content: center; gap: 9px;
    font-family: "Open Sans", Arial, sans-serif; font-size: 13px; color: var(--ink);
  }
  .contact-row { display: flex; align-items: center; gap: 16px; }
  .contact-item { display: flex; align-items: center; gap: 5px; white-space: nowrap; }
  .contact-icon { width: 12px; height: 12px; flex: none; }
  .contact-item--web { font-size: 15px; font-weight: 600; }
  .contact-item--web .contact-icon { width: 14px; height: 14px; }

  /* Brand side */
  .card--brand { border-left: 10px solid var(--teal); }
  .brand-pattern {
    position: absolute; inset: 0;
    background: linear-gradient(135deg, var(--pattern-base) 0%, var(--pattern-tint) 100%);
  }
  .brand-name {
    position: absolute; left: 0; right: 0; top: 118px; text-align: center;
    font-family: "Inconsolata", Consolas, monospace; font-weight: 600;
    font-size: 34px; letter-spacing: 4px; color: var(--teal); text-transform: uppercase;
  }
  .brand-url {
    position: absolute; left: 0; right: 0; top: 200px; text-align: center;
    font-family: "Inconsolata", Consolas, monospace; font-size: 13px;
    letter-spacing: 3px; color: var(--ink-soft);
  }
</style>
</head>
<body>
<main class="canvas">

  <section class="card card--info" aria-label="Card back: contact details">
    <div class="contact-list">
      <div class="contact-row">
        <span class="contact-item">
          <svg class="contact-icon" viewBox="0 0 12 12"><rect width="12" height="12" fill="var(--teal)"/><path d="M2 3.5h8v5H2z" fill="none" stroke="#fff" stroke-width="0.9"/><path d="M2 3.5l4 3 4-3" fill="none" stroke="#fff" stroke-width="0.9"/></svg>
          info@speakwithnadia.net
        </span>
      </div>
      <div class="contact-row">
        <span class="contact-item">
          <svg class="contact-icon" viewBox="0 0 12 12"><rect width="12" height="12" fill="var(--teal)"/></svg>
          @speakwithnadia
        </span>
        <span class="contact-item">
          <svg class="contact-icon" viewBox="0 0 12 12"><rect width="12" height="12" fill="var(--teal)"/></svg>
          /speakwithnadia
        </span>
        <span class="contact-item">
          <svg class="contact-icon" viewBox="0 0 12 12"><circle cx="6" cy="6" r="6" fill="var(--teal)"/></svg>
          speakwithnadia
        </span>
      </div>
      <div class="contact-row">
        <span class="contact-item contact-item--web">
          <svg class="contact-icon" viewBox="0 0 14 14"><circle cx="7" cy="7" r="7" fill="var(--teal)"/><circle cx="7" cy="7" r="4.5" fill="none" stroke="#fff" stroke-width="0.9"/><ellipse cx="7" cy="7" rx="2" ry="4.5" fill="none" stroke="#fff" stroke-width="0.9"/><path d="M2.5 7h9" stroke="#fff" stroke-width="0.9"/></svg>
          www.speakwithnadia.net
        </span>
      </div>
    </div>
  </section>

  <section class="card card--brand" aria-label="Card front: brand">
    <div class="brand-pattern" role="img" aria-label="Subtle repeating geometric pattern in pale teal on cream"></div>
    <p class="brand-name">Nadia Tutoring</p>
    <p class="brand-url">www.speakwithnadia.net</p>
  </section>

</main>
</body>
</html>
```